The Brandwell Firm

We need a new design for our letterhead and envelopes. We are a personal injury and criminal defense firm so we need something modern and clean, but more on the professional/traditional side. Our new logo has two colors and is attached to the file so we need something that works well with those colors/matches the design. The following information needs to be on the letterhead:
Phone: (555) 214-3370
Fax: (555) 214-5186
Toll-Free: (888) 431-2059
Post Office Box 4721
Millbrook, SC 29555-4721
HarmClaimCounsel.example
PalmettoTrialAdvocates.example

Target Market(s)

Clients, government agencies, other law firms

Industry/Entity Type

Legal

Font styles to use
Sans Serif
Other font styles liked:
• Arial

Colors

Designer to choose colors to be used in the design.

Requirements
Must have
• Must look professional and clean, modern
Nice to have
• I would like to see a design that works with the logo but does not distract from the content that will be printed on it
Should not have
• Too many colors or crazy designs.

```html
<!DOCTYPE html>
<html lang="en">
<head>
<meta charset="utf-8">
<title>The Brandwell Firm – Stationery</title>
<link href="https://fonts.googleapis.com/css2?family=Source+Sans+3:wght@400;600&display=swap" rel="stylesheet">
<style>
  :root {
    --backdrop: #7a7a7a;
    --paper: #f4f3f1;
    --firm-red: #d51f27;
    --firm-navy: #2e3192;
    --ink: #3a3a3a;
    --ink-soft: #4a4a4a;
  }
  * { box-sizing: border-box; margin: 0; padding: 0; }
  html, body { width: 1200px; height: 793px; overflow: hidden; }
  body {
    background: var(--backdrop);
    font-family: "Source Sans 3", Arial, sans-serif;
    color: var(--ink);
    position: relative;
  }
  .sheet {
    position: absolute;
    background: var(--paper);
    box-shadow: 0 2px 6px rgba(0,0,0,.25);
    overflow: hidden;
  }
  .band { position: absolute; left: 0; width: 100%; display: block; }
  .band--top { top: 0; height: 20px; }
  .band--bottom { bottom: 0; height: 20px; }

  .brand {
    display: flex; align-items: center; gap: 8px;
    color: var(--firm-navy); font-weight: 600; white-space: nowrap;
  }
  .brand__dot { width: 12px; height: 12px; border-radius: 50%; background: var(--firm-red); flex: none; }

  /* Letterhead */
  .letterhead { left: 82px; top: 62px; width: 475px; height: 668px; }
  .letterhead .brand { position: absolute; top: 116px; left: 0; width: 100%; justify-content: center; font-size: 22px; }
  .letter { position: absolute; left: 48px; top: 248px; width: 381px; }
  .letter__salutation { font-size: 13px; color: var(--ink-soft); margin-bottom: 22px; }
  .letter__body p { font-size: 7.2px; line-height: 11.3px; text-align: justify; margin-bottom: 11.5px; }
  .letter__closing { font-size: 7.4px; margin-top: 20px; }
  .letter__signature { display: block; width: 62px; height: 26px; margin: 6px 0 6px -2px; background: #dcdcde; }
  .letter__signer { font-size: 7.6px; line-height: 10px; }

  .letter-footer { position: absolute; left: 48px; top: 660px; width: 382px; top: auto; bottom: 34px; font-size: 8px; color: var(--ink-soft); }
  .letter-footer__rule { display: flex; align-items: center; gap: 3px; white-space: nowrap; margin-bottom: 9px; }
  .letter-footer__rule::before, .letter-footer__rule::after { content: ""; flex: 1; height: 1px; background: #333; }
  .letter-footer__rule b { font-weight: 600; }
  .letter-footer__cols { display: flex; justify-content: space-between; line-height: 11px; }
  .letter-footer__cols .web { text-align: right; }

  /* Envelope back */
  .envelope-back { left: 578px; top: 225px; width: 531px; height: 241px; }
  .envelope-back__flap { position: absolute; left: 0; top: 0; width: 531px; height: 90px; display: block; }
  .envelope-back .brand { position: absolute; top: 32px; left: 0; width: 100%; justify-content: center; font-size: 15px; color: #fff; }
  .envelope-back .brand__dot { width: 9px; height: 9px; background: #fff; }

  /* Envelope front */
  .envelope-front { left: 578px; top: 486px; width: 532px; height: 244px; }
  .envelope-front .brand { position: absolute; left: 27px; top: 52px; font-size: 22px; }
  .envelope-front__address { position: absolute; left: 36px; top: 107px; font-size: 8px; line-height: 10px; color: var(--ink-soft); }
</style>
</head>
<body>

<section class="sheet letterhead" aria-label="Letterhead">
  <svg class="band band--top" viewBox="0 0 475 20" preserveAspectRatio="none"><polygon points="0,0 475,0 475,1 0,19" fill="var(--firm-red)"/></svg>
  <div class="brand"><span class="brand__dot"></span>The Brandwell Firm</div>

  <article class="letter">
    <p class="letter__salutation">Dear Mr. Carter,</p>
    <div class="letter__body">
      <p>Lorem ipsum dolor sit amet, consectetur adipiscing elit. Donec orci purus, luctus vitae dignissim eu, iaculis sed purus. Vivamus faucibus, ipsum nec aliquet viverra, leo mauris condimentum ligula, sit amet sagittis enim ligula quis arcu. Nam egestas tortor id nisi porttitor mattis. In tortor ante, ultricies in suscipit a, tempus non massa. Vivamus et auctor mi. Fusce vel massa nulla. Phasellus nec eros mauris, et scelerisque orci.</p>
      <p>Donec malesuada orci vitae nulla accumsan porta a id massa. Quisque accumsan iaculis magna sit amet fringilla. Maecenas consequat, magna eget tincidunt semper, odio nibh rutrum mi, id feugiat ante nisi eu risus. Vestibulum nunc orci, rhoncus a placerat in, ultricies in mi. Cras mattis varius eros, vel fringilla nisi suscipit eget. Quisque scelerisque sagittis nulla at porttitor.</p>
      <p>Sed id augue vitae urna euismod commodo aliquet a quam. Pellentesque arcu velit, cursus et malesuada ut, consequat et diam. Nullam erat sem, rhoncus id ullamcorper vitae, rhoncus et arcu. In ultricies ultricies nulla, ut rutrum nisi iaculis at. Donec eu magna a metus ornare faucibus. Fusce aliquet faucibus ultricies. Morbi semper, est id tincidunt gravida, sem arcu adipiscing lacus, ac bibendum nulla leo eu purus. Quisque nec diam sed risus consectetur a accumsan quis quis nibh. Vestibulum id purus lorem.</p>
      <p>It is a long established fact that a reader will be distracted by the readable content of a page when looking at its layout. The point of using Lorem Ipsum is that it has a more-or-less normal distribution of letters, as opposed to using 'Content here, content here', making it look like readable English. Many desktop publishing packages</p>
    </div>
    <p class="letter__closing">Sincerely,</p>
    <span class="letter__signature" role="img" aria-label="Handwritten signature"></span>
    <p class="letter__signer">Daniel Hart<br>CEO/ Founder</p>
  </article>

  <footer class="letter-footer">
    <div class="letter-footer__rule"><span><b>TF</b>: (888) 431-2059 <b>P</b>: (555) 214-3370 <b>F</b>: (555) 214-5186</span></div>
    <div class="letter-footer__cols">
      <p>Post Office Box 4721<br>Millbrook, SC 29555-4721</p>
      <p class="web">HarmClaimCounsel.example<br>PalmettoTrialAdvocates.example</p>
    </div>
  </footer>
  <svg class="band band--bottom" viewBox="0 0 475 20" preserveAspectRatio="none"><polygon points="0,20 475,20 475,1 0,19" fill="var(--firm-navy)"/></svg>
</section>

<section class="sheet envelope-back" aria-label="Envelope back">
  <svg class="envelope-back__flap" viewBox="0 0 531 90"><path d="M0,0 H531 L520,72 Q517,88 500,88 H31 Q14,88 11,72 Z" fill="var(--firm-navy)"/></svg>
  <div class="brand"><span class="brand__dot"></span>The Brandwell Firm</div>
</section>

<section class="sheet envelope-front" aria-label="Envelope front">
  <svg class="band band--top" viewBox="0 0 532 20" preserveAspectRatio="none"><polygon points="0,0 532,0 532,1 0,19" fill="var(--firm-red)"/></svg>
  <div class="brand"><span class="brand__dot"></span>The Brandwell Firm</div>
  <p class="envelope-front__address">Post Office Box 4721<br>Millbrook, SC 29555-4721</p>
  <svg class="band band--bottom" viewBox="0 0 532 20" preserveAspectRatio="none"><polygon points="0,20 532,20 532,1 0,19" fill="var(--firm-navy)"/></svg>
</section>

</body>
</html>
```